Bookmark Design

We would like to design a book mark with logos of our two business and a quote.

One side with the quote "The first wealth is health" - Tobias Kendrick Mallory and the two logos.

The back side has the two logos with its respective phone numbers and a common address (this is to be advised to the winner of the project).

```html
<!DOCTYPE html>
<html lang="en">
<head>
<meta charset="utf-8">
<title>Bookmark Design</title>
<link rel="stylesheet" href="https://fonts.googleapis.com/css2?family=Oswald:wght@500&family=Yellowtail&family=Ubuntu:wght@400;500;700&display=swap">
<style>
  :root {
    --page: #ffffff;
    --frame-top: #6f86b8;
    --frame-mid: #7fbf9f;
    --frame-bottom: #cfdadd;
    --panel-top: #dde0ea;
    --panel: #ffffff;
    --quote-teal: #2f7a6c;
    --quote-shadow: #c6ced4;
    --ink: #3d4a55;
    --dental-green: #5db35e;
    --clinic-blue: #1d5aa6;
    --rule: #b9c0c6;
  }
  * { margin: 0; padding: 0; box-sizing: border-box; }
  html, body { width: 1200px; height: 849px; overflow: hidden; background: var(--page); }
  .canvas { position: relative; width: 1200px; height: 849px; }
  .bookmark { position: absolute; top: 116px; width: 205px; height: 613px; }
  .bookmark--front { left: 312px; }
  .bookmark--back { left: 675px; }
  .bookmark__shape { position: absolute; inset: 0; }
  .bookmark__item {
    position: absolute; left: 0; width: 205px; text-align: center;
    font-family: "Ubuntu", sans-serif; color: var(--ink);
  }
  .divider { top: 78px; font-size: 9px; letter-spacing: 3px; color: var(--ink); }
  .divider--lower { top: 334px; }
  .quote-line { font-family: "Oswald", sans-serif; font-weight: 500; color: var(--quote-teal);
    text-shadow: 1px 1px 0 var(--quote-shadow); line-height: 1; }
  .quote-line--first { top: 116px; font-size: 23px; }
  .quote-line--is { top: 197px; font-size: 23px; }
  .quote-script { font-family: "Yellowtail", cursive; color: var(--quote-teal);
    text-shadow: 2px 2px 0 var(--quote-shadow); font-size: 44px; line-height: 1; }
  .quote-script--wealth { top: 146px; }
  .quote-script--health { top: 224px; }
  .quote-author { top: 296px; font-size: 9px; letter-spacing: 0.3px; }
  .brand { display: flex; align-items: center; justify-content: center; gap: 6px;
    font-family: "Ubuntu", sans-serif; font-weight: 700; font-size: 17px; line-height: 1; }
  .brand__dot { width: 14px; height: 14px; border-radius: 50%; flex: none; }
  .brand--dental { color: var(--dental-green); }
  .brand--dental .brand__dot { background: var(--dental-green); }
  .brand--clinic { color: var(--clinic-blue); }
  .brand--clinic .brand__dot { background: var(--clinic-blue); }
  .bookmark--front .brand--dental { top: 408px; }
  .bookmark--front .brand--clinic { top: 518px; }
  .bookmark--back .brand--dental { top: 186px; }
  .bookmark--back .brand--clinic { top: 326px; }
  .phone { font-weight: 500; font-size: 11px; }
  .phone span { display: inline-block; padding-bottom: 2px; border-bottom: 1px dashed var(--rule); }
  .phone--dental { top: 245px; }
  .phone--clinic { top: 399px; }
  .address { top: 449px; font-weight: 500; font-size: 11px; line-height: 14px; }
</style>
</head>
<body>
<main class="canvas">

  <section class="bookmark bookmark--front" aria-label="Bookmark front">
    <svg class="bookmark__shape" viewBox="0 0 205 613" width="205" height="613" aria-hidden="true">
      <defs>
        <linearGradient id="frameFront" x1="0" y1="0" x2="0" y2="1">
          <stop offset="0.2" stop-color="var(--frame-top)"/>
          <stop offset="0.6" stop-color="var(--frame-mid)"/>
          <stop offset="1" stop-color="var(--frame-bottom)"/>
        </linearGradient>
        <linearGradient id="panelFront" x1="0" y1="0" x2="0" y2="1">
          <stop offset="0" stop-color="var(--panel-top)"/>
          <stop offset="0.25" stop-color="var(--panel)"/>
          <stop offset="1" stop-color="var(--panel)"/>
        </linearGradient>
      </defs>
      <path d="M0 80 Q0 66 12 58 L93 5 Q102 0 111 5 L193 58 Q205 66 205 80 L205 600 Q205 613 192 613 L13 613 Q0 613 0 600 Z" fill="url(#frameFront)"/>
      <path d="M11 84 Q11 74 20 68 L94 18 Q102 13 110 18 L185 68 Q194 74 194 84 L194 588 Q194 600 182 600 L23 600 Q11 600 11 588 Z" fill="url(#panelFront)"/>
      <circle cx="103" cy="34" r="6" fill="#fff" stroke="#cfd4dc" stroke-width="1"/>
    </svg>
    <p class="bookmark__item divider">- • • • • • • • -</p>
    <p class="bookmark__item quote-line quote-line--first">THE FIRST</p>
    <p class="bookmark__item quote-script quote-script--wealth">Wealth</p>
    <p class="bookmark__item quote-line quote-line--is">IS</p>
    <p class="bookmark__item quote-script quote-script--health">Health</p>
    <p class="bookmark__item quote-author">- TOBIAS KENDRICK MALLORY -</p>
    <p class="bookmark__item divider divider--lower">- • • • • • • • -</p>
    <p class="bookmark__item brand brand--dental"><span class="brand__dot"></span>Northgate Dental</p>
    <p class="bookmark__item brand brand--clinic"><span class="brand__dot"></span>Brightwood Clinic</p>
  </section>

  <section class="bookmark bookmark--back" aria-label="Bookmark back">
    <svg class="bookmark__shape" viewBox="0 0 205 613" width="205" height="613" aria-hidden="true">
      <defs>
        <linearGradient id="frameBack" x1="0" y1="0" x2="0" y2="1">
          <stop offset="0.2" stop-color="var(--frame-top)"/>
          <stop offset="0.6" stop-color="var(--frame-mid)"/>
          <stop offset="1" stop-color="var(--frame-bottom)"/>
        </linearGradient>
        <linearGradient id="panelBack" x1="0" y1="0" x2="0" y2="1">
          <stop offset="0" stop-color="var(--panel-top)"/>
          <stop offset="0.25" stop-color="var(--panel)"/>
          <stop offset="1" stop-color="var(--panel)"/>
        </linearGradient>
      </defs>
      <path d="M0 80 Q0 66 12 58 L93 5 Q102 0 111 5 L193 58 Q205 66 205 80 L205 600 Q205 613 192 613 L13 613 Q0 613 0 600 Z" fill="url(#frameBack)"/>
      <path d="M11 84 Q11 74 20 68 L94 18 Q102 13 110 18 L185 68 Q194 74 194 84 L194 588 Q194 600 182 600 L23 600 Q11 600 11 588 Z" fill="url(#panelBack)"/>
      <circle cx="103" cy="34" r="6" fill="#fff" stroke="#cfd4dc" stroke-width="1"/>
    </svg>
    <p class="bookmark__item brand brand--dental"><span class="brand__dot"></span>Northgate Dental</p>
    <p class="bookmark__item phone phone--dental"><span>Phone#: (02) 5550-1827</span></p>
    <p class="bookmark__item brand brand--clinic"><span class="brand__dot"></span>Brightwood Clinic</p>
    <p class="bookmark__item phone phone--clinic"><span>Phone#: (02) 5550-1827</span></p>
    <p class="bookmark__item address">Adress:<br>14 Harbour Lane<br>KELLAWAY, New South<br>Wales(NSW), 2590</p>
  </section>

</main>
</body>
</html>
```